The most modern business card ever !!!

Our company call “Vendalo”. Vendalo is a technology company specialized in cruises solutions. Out main product is a platform to reserve cruises. This is a revolutionary platform that make easier to travel agencies and final users to reserve cruises across dozen companies like tibba, wernu, hpv, dgb, etc..We are a “start up”, with a young team of developers and we want to transmit it.. For it, we want something different, a modern business card that represent cruises and technology.. When someone receive this card, this person should say: wowww this is different… this is modern… this is a cruise related company..
- diferent, modern
- traditions business card

```html
<!DOCTYPE html>
<html lang="en">
<head>
<meta charset="UTF-8">
<title>Vendalo – Business Card</title>
<link href="https://fonts.googleapis.com/css2?family=Open+Sans:wght@400;600;700&display=swap" rel="stylesheet">
<style>
  :root {
    --page-bg: #e9e7e4;
    --card-dark: #000000;
    --brand-blue: #29a9e1;
    --stripe-white: #f3f2f0;
    --text-white: #ffffff;
    --text-grey: #c9c9c9;
  }
  * { margin: 0; padding: 0; box-sizing: border-box; }
  html, body {
    width: 1200px; height: 900px; overflow: hidden;
    background: var(--page-bg);
    font-family: "Open Sans", Arial, sans-serif;
  }
  .business-card {
    position: absolute; left: 160px; top: 178px;
    width: 880px; height: 544px;
    display: flex;
    box-shadow: 0 10px 30px rgba(0,0,0,0.18);
  }
  .card-info {
    width: 494px; height: 100%;
    background: var(--card-dark);
    padding: 62px 0 0 54px;
    color: var(--text-grey);
  }
  .brand-name {
    font-size: 62px; font-weight: 600; color: var(--text-white);
    letter-spacing: 1px; line-height: 1;
  }
  .person-name {
    margin-top: 98px;
    font-size: 27px; font-weight: 700; color: var(--brand-blue);
    letter-spacing: 0.5px; line-height: 1.1;
  }
  .person-role { font-size: 24px; line-height: 1.35; }
  .contact-list { list-style: none; margin-top: 14px; }
  .contact-list li {
    display: flex; align-items: center; gap: 8px;
    font-size: 24px; line-height: 32px;
  }
  .contact-icon { width: 20px; height: 20px; fill: var(--brand-blue); flex: none; }
  .postal-address { margin-top: 12px; font-size: 24px; line-height: 31px; font-style: normal; }
  .card-accent-stripe { width: 47px; height: 100%; background: var(--stripe-white); }
  .card-accent-panel { flex: 1; height: 100%; background: var(--brand-blue); }
</style>
</head>
<body>
  <div class="business-card">
    <section class="card-info">
      <div class="brand-name">Vendalo</div>
      <div class="person-name">MARCUS ELLERY</div>
      <div class="person-role">Managing Director</div>
      <ul class="contact-list">
        <li>
          <svg class="contact-icon" viewBox="0 0 20 20"><path d="M2 7c0-2 3-4 8-4s8 2 8 4v2h-4V7.5c-1-.6-2.4-.9-4-.9s-3 .3-4 .9V9H2zM5 10h10l2 6H3z"/></svg>
          061-482 735 190
        </li>
        <li>
          <svg class="contact-icon" viewBox="0 0 20 20"><path d="M6 1h8a1 1 0 0 1 1 1v16a1 1 0 0 1-1 1H6a1 1 0 0 1-1-1V2a1 1 0 0 1 1-1zm1 3v11h6V4zm3 12a1 1 0 1 0 0 2 1 1 0 0 0 0-2z"/></svg>
          061-482 735 190
        </li>
        <li>
          <svg class="contact-icon" viewBox="0 0 20 20"><path d="M2 4h16v12H2zm1.5 1.5L10 11l6.5-5.5z"/></svg>
          hello@vendalo.io
        </li>
        <li>
          <svg class="contact-icon" viewBox="0 0 20 20"><circle cx="10" cy="10" r="8"/><path d="M4 8c2 0 3 1 3 3s2 2 2 4M13 4c-1 2 0 3 2 3s2 2 3 1" stroke="#000" stroke-width="1.4" fill="none"/></svg>
          www.vendalo.io
        </li>
      </ul>
      <address class="postal-address">48 Harbour Quay, Suite 7<br>Portmere, 204815</address>
    </section>
    <div class="card-accent-stripe"></div>
    <div class="card-accent-panel"></div>
  </div>
</body>
</html>
```